Hello my Name is Elias Moreno. I buy and sell vintage comic books, you can refer to my instragram page qpkz.comics to get ideas and inspiration. For the front of the card I would like my company logo QPKZ Comics with a yellow and black background with the bat signal or bat emblem like on my IG page and with my info Elias Moreno as the Owner and address/ phone number, PO Box 617283, Miami, FL 33827, 305-482-6170 and that I buy and sell comics & collectables . Also feel free to be open to other ideas if you want. Im not stuck on one design. For the back of the card I would like for it to say follow me on Instagram QPKZ.Comics with the ig emblem. Also would like the card to be vertical if possible. Thanks

```html
<!DOCTYPE html>
<html lang="en">
<head>
<meta charset="utf-8">
<title>QPKZ Comics – Business Card</title>
<link rel="stylesheet" href="https://fonts.googleapis.com/css2?family=Open+Sans:ital,wght@0,400;0,600;0,700;1,700&display=swap">
<style>
  :root {
    --canvas: #ecebe9;
    --card: #222b33;
    --yellow: #f6e51c;
    --white: #ffffff;
    --muted: #e4e6e8;
    --rule: #8a8450;
  }
  * { box-sizing: border-box; margin: 0; padding: 0; }
  html, body {
    width: 1200px; height: 900px; overflow: hidden;
    background: var(--canvas);
    font-family: "Open Sans", Arial, sans-serif;
  }
  .canvas { position: relative; width: 1200px; height: 900px; }

  .card {
    position: absolute;
    background: var(--card);
    box-shadow: 0 6px 18px rgba(0,0,0,0.25);
  }
  .card--front { left: 238px; top: 62px; width: 555px; height: 342px; }
  .card--back  { left: 457px; top: 518px; width: 560px; height: 343px; }

  /* Brand lockup */
  .brand {
    position: absolute;
    display: flex; align-items: center; gap: 10px;
  }
  .brand__dot { width: 18px; height: 18px; border-radius: 50%; flex: none; }
  .brand__name {
    font-weight: 700; font-size: 34px; line-height: 1.05; text-align: center;
  }
  .card--front .brand { left: 78px; top: 134px; }
  .card--front .brand__dot { background: var(--yellow); }
  .card--front .brand__name { color: var(--yellow); }
  .card--back .brand { left: 0; right: 0; top: 130px; justify-content: center; }
  .card--back .brand__dot { background: var(--white); }
  .card--back .brand__name { color: var(--white); font-size: 38px; }

  .divider {
    position: absolute; left: 265px; top: 82px;
    width: 1px; height: 174px; background: var(--rule);
  }

  .owner { position: absolute; left: 290px; top: 96px; }
  .owner__name {
    color: var(--yellow); font-weight: 700; font-size: 22px;
    letter-spacing: 0.3px; line-height: 1.2;
  }
  .owner__role { color: var(--muted); font-size: 14px; line-height: 1.3; }

  .contact { position: absolute; left: 290px; top: 176px; list-style: none; }
  .contact__item {
    display: flex; align-items: flex-start; gap: 5px;
    color: var(--muted); font-size: 14.5px; line-height: 20px;
    margin-bottom: 6px;
  }
  .contact__icon { width: 14px; height: 16px; flex: none; margin-top: 2px; }

  .tagline {
    position: absolute; left: 0; right: 0; top: 287px;
    text-align: center; color: var(--yellow);
    font-weight: 700; font-size: 16px; letter-spacing: 0.1px;
  }

  .social {
    position: absolute; left: 0; right: 0; top: 279px;
    display: flex; align-items: center; justify-content: center; gap: 12px;
    color: var(--white);
  }
  .social__label { font-weight: 700; font-style: italic; font-size: 19px; }
  .social__badge { width: 36px; height: 36px; border-radius: 50%; background: var(--yellow); }
  .social__handle { font-weight: 600; font-size: 19px; }
</style>
</head>
<body>
<main class="canvas">

  <section class="card card--front" aria-label="Card front">
    <div class="brand">
      <span class="brand__dot"></span>
      <span class="brand__name">QPKZ<br>Comics</span>
    </div>

    <div class="divider"></div>

    <div class="owner">
      <p class="owner__name">ELIAS MORENO</p>
      <p class="owner__role">Owner</p>
    </div>

    <ul class="contact">
      <li class="contact__item">
        <svg class="contact__icon" viewBox="0 0 16 16" aria-hidden="true">
          <path fill="#f6e51c" d="M3.6 1.2l2.3 2.6c.4.4.3 1-.1 1.4L4.6 6.3c.9 2 2.6 3.8 4.7 4.8l1.1-1.2c.4-.4 1-.4 1.4-.1l2.6 2.2c.4.4.5 1 .1 1.4l-1.3 1.4c-.6.6-1.5.8-2.3.5C6 13.8 2.3 10 .9 4.9.7 4.1.9 3.3 1.5 2.7l1.3-1.4c.2-.3.6-.3.8-.1z"/>
        </svg>
        <span>305-482-6170</span>
      </li>
      <li class="contact__item">
        <svg class="contact__icon" viewBox="0 0 14 18" aria-hidden="true">
          <path fill="#f6e51c" d="M7 0C3.4 0 .6 2.8.6 6.3 .6 11 7 18 7 18s6.4-7 6.4-11.7C13.4 2.8 10.6 0 7 0zm0 8.8a2.5 2.5 0 110-5 2.5 2.5 0 010 5z"/>
        </svg>
        <span>PO Box 617283, Miami,<br>FL 33827</span>
      </li>
    </ul>

    <p class="tagline">WE BUY AND SELL COMICS &amp; COLLECTABLES</p>
  </section>

  <section class="card card--back" aria-label="Card back">
    <div class="brand">
      <span class="brand__dot"></span>
      <span class="brand__name">QPKZ<br>Comics</span>
    </div>

    <div class="social">
      <span class="social__label">FOLLOW ME ON</span>
      <span class="social__badge"></span>
      <span class="social__handle">QPKZ.Comics</span>
    </div>
  </section>

</main>
</body>
</html>
```